Business Card for Air Cargo Brokerage

Hi Craftquorum -

Please see the images attached. I need a business card with a similar image and format but modernized. Business card should be portrait and have room for a QR code.

Thanks

```html
<!DOCTYPE html>
<html lang="en">
<head>
<meta charset="utf-8">
<title>Skyward Freight – Business Card</title>
<link href="https://fonts.googleapis.com/css2?family=Montserrat:wght@400;500;700;800&display=swap" rel="stylesheet">
<style>
  :root {
    --stage: #2a2a2a;
    --ink: #111111;
    --card-dark: #141414;
    --paper: #ffffff;
    --muted: #c4c4c4;
    --rule: #8a8a8a;
  }
  * { margin: 0; padding: 0; box-sizing: border-box; }
  html, body {
    width: 1200px; height: 900px; overflow: hidden;
    background: var(--stage);
    font-family: "Montserrat", sans-serif;
  }
  .stage { position: relative; width: 1200px; height: 900px; }

  .card {
    position: absolute; top: 80px;
    width: 420px; height: 740px;
    border-radius: 30px; overflow: hidden;
    background: var(--card-dark);
    box-shadow: 0 18px 40px rgba(0,0,0,.45);
  }
  .card-front { left: 160px; }
  .card-back  { left: 620px; }

  .front-art { position: absolute; inset: 0; width: 100%; height: 100%; }

  .brand {
    position: absolute; top: 118px; left: 0; right: 0;
    text-align: center; color: var(--ink);
  }
  .brand-name {
    font-weight: 800; font-size: 33px; letter-spacing: -0.5px;
    display: inline-flex; align-items: center; gap: 10px;
  }
  .brand-dot { width: 13px; height: 13px; border-radius: 50%; background: var(--ink); }
  .brand-tagline {
    margin-top: 4px; font-size: 12px; font-weight: 500; letter-spacing: 1.1px;
  }

  .person {
    position: absolute; top: 546px; left: 0; right: 0;
    text-align: center; color: var(--paper);
  }
  .person-name { font-size: 29px; font-weight: 700; line-height: 1.15; }
  .person-role { font-size: 15px; color: var(--muted); margin-top: 2px; }

  .contact-icons {
    position: absolute; top: 614px; left: 0; right: 0;
    display: flex; justify-content: center; align-items: center; gap: 6px;
  }
  .contact-icons .rule { width: 34px; height: 1px; background: var(--rule); margin: 0 8px; }
  .icon-tile {
    width: 22px; height: 22px; border-radius: 4px; background: var(--paper);
    display: flex; align-items: center; justify-content: center;
  }
  .contact-lines {
    position: absolute; top: 648px; left: 0; right: 0;
    text-align: center; color: var(--paper); font-size: 15px; line-height: 1.4;
  }

  .back-pattern { position: absolute; inset: 0; width: 100%; height: 100%; }
  .back-mark {
    position: absolute; right: 26px; bottom: 30px;
    display: flex; align-items: center; gap: 8px;
    color: var(--paper); font-weight: 800; font-size: 16px;
  }
  .back-mark .brand-dot { background: var(--paper); width: 10px; height: 10px; }
</style>
</head>
<body>
<main class="stage">

  <section class="card card-front" aria-label="Card front">
    <svg class="front-art" viewBox="0 0 420 740" aria-hidden="true">
      <defs>
        <linearGradient id="trailTone" x1="0" y1="1" x2="1" y2="0">
          <stop offset="0" stop-color="#f2f2f2"/>
          <stop offset="0.45" stop-color="#a8a8a8"/>
          <stop offset="1" stop-color="#3a3a3a"/>
        </linearGradient>
      </defs>
      <path d="M0 0 H420 V235 C340 250 310 340 280 420 C245 505 150 548 0 575 Z" fill="#ffffff"/>
    </svg>
    <svg class="front-art" viewBox="0 0 420 740" role="img" aria-label="Illustration of a cargo plane climbing to the upper right with curved grey vapour trails">
      <path d="M30 505 C55 420 140 345 250 300 L380 255 C385 330 345 410 275 460 C200 510 110 530 30 505 Z" fill="url(#trailTone)"/>
    </svg>

    <div class="brand">
      <div class="brand-name"><span class="brand-dot"></span>Skyward Freight</div>
      <div class="brand-tagline">SOLUTIONS FOR GLOBAL AIR COMMERCE</div>
    </div>

    <div class="person">
      <div class="person-name">Daniel Hart</div>
      <div class="person-role">Managing Director</div>
    </div>

    <div class="contact-icons">
      <span class="rule"></span>
      <span class="icon-tile" aria-label="Phone">
        <svg width="14" height="14" viewBox="0 0 24 24"><path d="M6.6 10.8a15 15 0 0 0 6.6 6.6l2.2-2.2a1 1 0 0 1 1-.25 11.4 11.4 0 0 0 3.6.57 1 1 0 0 1 1 1V20a1 1 0 0 1-1 1A17 17 0 0 1 3 4a1 1 0 0 1 1-1h3.5a1 1 0 0 1 1 1c0 1.25.2 2.45.57 3.6a1 1 0 0 1-.25 1z" fill="#111"/></svg>
      </span>
      <span class="icon-tile" aria-label="Email">
        <svg width="14" height="14" viewBox="0 0 24 24"><rect x="2" y="5" width="20" height="14" rx="2" fill="#111"/><path d="M3 6l9 7 9-7" stroke="#fff" stroke-width="1.8" fill="none"/></svg>
      </span>
      <span class="icon-tile" aria-label="Website">
        <svg width="14" height="14" viewBox="0 0 24 24"><circle cx="12" cy="12" r="9" fill="none" stroke="#111" stroke-width="2"/><path d="M3 12h18M12 3c3 3 3 15 0 18M12 3c-3 3-3 15 0 18" stroke="#111" stroke-width="1.6" fill="none"/></svg>
      </span>
      <span class="rule"></span>
    </div>

    <div class="contact-lines">
      555-014-2290<br>
      info@harborlinegroup.com<br>
      www.harborlinegroup.com
    </div>
  </section>

  <section class="card card-back" aria-label="Card back">
    <svg class="back-pattern" viewBox="0 0 420 740" role="img" aria-label="Glossy repeating pattern of small plane marks in silver and black tones">
      <defs>
        <linearGradient id="backBase" x1="0" y1="0" x2="0.6" y2="1">
          <stop offset="0" stop-color="#2c2c2c"/>
          <stop offset="0.5" stop-color="#161616"/>
          <stop offset="1" stop-color="#0b0b0b"/>
        </linearGradient>
        <radialGradient id="backSheen" cx="0.7" cy="0.08" r="0.6">
          <stop offset="0" stop-color="#8a8a8a" stop-opacity="0.55"/>
          <stop offset="1" stop-color="#8a8a8a" stop-opacity="0"/>
        </radialGradient>
      </defs>
      <rect width="420" height="740" fill="url(#backBase)"/>
      <rect width="420" height="740" fill="url(#backSheen)"/>
    </svg>
    <div class="back-mark"><span class="brand-dot"></span>Skyward Freight</div>
  </section>

</main>
</body>
</html>
```